Hacienda Monte Verda Business cards

We would like 3 individual business cards with the logo you designed:

1) Marta Pellingford - Phone: 206 555 0147
2) Theodore R Pellingford - Phone 206 555 0183
3) Dana Moreth - Phone 310-555-0162

Address for all three cards:
7218 142nd Ave NE
Larkfield, WA 98071
HaciendaMonteVerda@brindlemail.com

```html
<!DOCTYPE html>
<html lang="en">
<head>
<meta charset="utf-8">
<title>Hacienda Monte Verda – Business Card</title>
<link rel="stylesheet" href="https://fonts.googleapis.com/css2?family=Questrial&display=swap">
<style>
  :root {
    --backdrop: #8f8a84;
    --card-white: #ffffff;
    --card-mist: #e2e2e2;
    --band-black: #050505;
    --logo-ink: #1c1c1c;
    --contact-ink: #e8e8e8;
    --name-ink: #dedede;
    --scene-light: #d9d9d9;
    --scene-mid: #c2c2c2;
  }
  * { box-sizing: border-box; margin: 0; padding: 0; }
  html, body {
    width: 1200px;
    height: 871px;
    overflow: hidden;
    background: var(--backdrop);
  }
  body { position: relative; font-family: "Questrial", sans-serif; }

  .business-card {
    position: absolute;
    left: 100px;
    top: 150px;
    width: 1000px;
    height: 571px;
    background: var(--band-black);
    box-shadow: 0 18px 40px rgba(0,0,0,0.35);
    overflow: hidden;
  }
  .card-header {
    position: absolute;
    left: 0; top: 0;
    width: 100%;
    height: 262px;
    background: linear-gradient(180deg, var(--card-white) 0%, var(--card-white) 45%, var(--card-mist) 100%);
  }
  .brand-mark {
    position: absolute;
    left: 110px;
    top: 150px;
    display: flex;
    align-items: center;
    gap: 12px;
    color: var(--logo-ink);
    font-size: 28px;
    letter-spacing: 1px;
    white-space: nowrap;
  }
  .brand-mark .brand-dot {
    width: 14px; height: 14px;
    border-radius: 50%;
    background: var(--logo-ink);
  }
  .pasture-scene {
    position: absolute;
    left: 600px;
    top: 30px;
    width: 370px;
    height: 232px;
    background: radial-gradient(ellipse at 40% 45%, var(--scene-mid) 0%, var(--scene-light) 55%, rgba(226,226,226,0) 100%);
  }

  .contact-list {
    position: absolute;
    left: 100px;
    top: 296px;
    list-style: none;
    color: var(--contact-ink);
    font-size: 16px;
    line-height: 1;
  }
  .contact-list li {
    display: flex;
    align-items: center;
    height: 32px;
  }
  .contact-list .icon {
    width: 30px;
    display: flex;
    justify-content: flex-start;
  }
  .contact-list .icon svg { display: block; }

  .holder-name {
    position: absolute;
    left: 600px;
    top: 294px;
    color: var(--name-ink);
    font-size: 24px;
    letter-spacing: 1px;
    white-space: nowrap;
  }
</style>
</head>
<body>
  <article class="business-card">
    <header class="card-header">
      <div class="brand-mark">
        <span class="brand-dot"></span>
        <span class="brand-name">Hacienda Monte Verda</span>
      </div>
      <div class="pasture-scene" role="img" aria-label="Faint silhouette of a large oak tree beside a fenced pasture with grazing horses"></div>
    </header>

    <ul class="contact-list">
      <li>
        <span class="icon">
          <svg width="12" height="18" viewBox="0 0 12 18" fill="none" stroke="currentColor" stroke-width="1.5">
            <rect x="1" y="1" width="10" height="16" rx="2"/>
            <line x1="4.5" y1="14" x2="7.5" y2="14"/>
          </svg>
        </span>
        <span>206 555 0147</span>
      </li>
      <li>
        <span class="icon">
          <svg width="14" height="18" viewBox="0 0 14 18" fill="none" stroke="currentColor" stroke-width="1.5">
            <path d="M7 17 C7 17 1 10.5 1 6.5 A6 6 0 0 1 13 6.5 C13 10.5 7 17 7 17 Z"/>
            <circle cx="7" cy="6.5" r="2"/>
          </svg>
        </span>
        <span>7218 142nd Ave NE</span>
      </li>
      <li>
        <span class="icon"></span>
        <span>Larkfield, WA 98071</span>
      </li>
      <li>
        <span class="icon">
          <svg width="16" height="12" viewBox="0 0 16 12" fill="none" stroke="currentColor" stroke-width="1.5">
            <rect x="1" y="1" width="14" height="10"/>
            <polyline points="1,1 8,7 15,1"/>
          </svg>
        </span>
        <span>HaciendaMonteVerda@brindlemail.com</span>
      </li>
    </ul>

    <p class="holder-name">Marta Pellingford</p>
  </article>
</body>
</html>
```